Verdant Systems Business Card

want the back of card to be blue- with the logo in the center
front of card- info plus logo (info being mailing address, email address, and website address )
4 different names with titles to have on cards
1) Calvin Borsted - Owner
2) Naomi Trelvik- Customer Relationship Specialist
3) Felix Andrade- Vice President of Sales
4) Owen Markby- Chief Technology Officer

Target Market(s)

tech company in the government/probation office industry

Industry/Entity Type

Government Office

Contact Information for Business Card

1) Calvin Borsted - Owner

Colors
0355a3
ffffff

Requirements
Must have
• back side should be blue, with the logo placed in the center
• front side needs to include both the logo, as well as company info (info should include website address, email address, and mailing address)

```html
<!DOCTYPE html>
<html lang="en">
<head>
<meta charset="utf-8">
<title>Verdant Systems Business Card</title>
<link rel="stylesheet" href="https://fonts.googleapis.com/css2?family=Crimson+Text:wght@400&family=Montserrat:wght@400;500&display=swap">
<style>
  :root {
    --navy: #152c55;
    --white: #ffffff;
    --grey: #8a8f99;
    --page: #f2f2f2;
    --serif: "Crimson Text", "Times New Roman", serif;
    --sans: "Montserrat", Arial, sans-serif;
  }
  * { box-sizing: border-box; margin: 0; padding: 0; }
  html, body { width: 1200px; height: 1200px; overflow: hidden; background: var(--page); }
  .sheet {
    width: 1200px; height: 1200px;
    display: flex; flex-direction: column; align-items: center; justify-content: center; gap: 40px;
  }
  .card {
    position: relative; width: 900px; height: 527px; overflow: hidden;
    box-shadow: 0 2px 10px rgba(0,0,0,0.08);
  }
  .card--back { background: var(--navy); }
  .card--front { background: var(--white); }

  .brand { position: absolute; left: 0; right: 0; display: flex; flex-direction: column; align-items: center; }
  .brand__dot { width: 78px; height: 78px; border-radius: 50%; }
  .brand__name { font-family: var(--serif); font-weight: 400; line-height: 1; margin-top: 18px; letter-spacing: 1px; }
  .card--back .brand { top: 150px; }
  .card--back .brand__dot { background: var(--white); width: 96px; height: 96px; }
  .card--back .brand__name { color: var(--white); font-size: 64px; }
  .card--front .brand { top: 52px; }
  .card--front .brand__dot { background: var(--navy); }
  .card--front .brand__name { color: var(--navy); font-size: 54px; }

  .name-band {
    position: absolute; left: 0; top: 298px; width: 498px; height: 47px;
    background: var(--navy); color: var(--white);
    font-family: var(--serif); font-size: 34px; line-height: 47px;
    text-align: right; padding-right: 22px;
  }
  .title {
    position: absolute; left: 506px; top: 298px; line-height: 47px;
    font-family: var(--serif); font-size: 34px; color: var(--grey);
  }
  .title-rule { position: absolute; left: 620px; top: 324px; width: 246px; height: 3px; background: var(--navy); }

  .contact { position: absolute; left: 0; right: 0; top: 375px; font-family: var(--sans); color: var(--navy); }
  .contact__address { text-align: center; font-size: 21px; margin-bottom: 14px; }
  .contact__row { display: flex; justify-content: center; gap: 36px; font-size: 19.5px; margin-bottom: 8px; }
  .contact__item { display: flex; align-items: center; gap: 6px; white-space: nowrap; }
  .contact__item svg { width: 18px; height: 18px; fill: none; stroke: var(--grey); stroke-width: 2; }
</style>
</head>
<body>
<main class="sheet">

  <section class="card card--back" aria-label="Card back">
    <div class="brand">
      <span class="brand__dot"></span>
      <span class="brand__name">VERDANT SYSTEMS</span>
    </div>
  </section>

  <section class="card card--front" aria-label="Card front">
    <div class="brand">
      <span class="brand__dot"></span>
      <span class="brand__name">VERDANT SYSTEMS</span>
    </div>

    <div class="name-band">Calvin Borsted</div>
    <div class="title">Owner</div>
    <div class="title-rule"></div>

    <div class="contact">
      <p class="contact__address">Your Full Address Comes here</p>
      <div class="contact__row">
        <span class="contact__item">
          <svg viewBox="0 0 20 20"><path d="M5 2l3 4-2 2c1 3 3 5 6 6l2-2 4 3-2 3C9 18 2 11 2 4z"/></svg>: (000) 000-0000
        </span>
        <span class="contact__item">
          <svg viewBox="0 0 20 20"><rect x="5" y="2" width="10" height="5"/><rect x="2" y="7" width="16" height="7"/><rect x="5" y="12" width="10" height="6"/></svg>: (000) 000-0000
        </span>
        <span class="contact__item">
          <svg viewBox="0 0 20 20"><rect x="5" y="2" width="10" height="16" rx="2"/><line x1="9" y1="15" x2="11" y2="15"/></svg>: (000) 000-0000
        </span>
      </div>
      <div class="contact__row">
        <span class="contact__item">
          <svg viewBox="0 0 20 20"><rect x="2" y="4" width="16" height="12"/><path d="M2 4l8 7 8-7"/></svg>: info@verdantsystems.net
        </span>
        <span class="contact__item">
          <svg viewBox="0 0 20 20"><circle cx="10" cy="10" r="8"/><ellipse cx="10" cy="10" rx="3.5" ry="8"/><line x1="2" y1="10" x2="18" y2="10"/></svg>: www.verdantsystems.net
        </span>
      </div>
    </div>
  </section>

</main>
</body>
</html>
```